Marwick Law Letterhead

We need a new letterhead design for a Law Firm. The address for the law firm is 1475 Calloway Street, Suite 210, Houston, Texas 77041. Phone Number: 832-361-9027; Fax Number: 832-614-7359. The logo is uploaded to the project.

```html
<!DOCTYPE html>
<html lang="en">
<head>
<meta charset="utf-8">
<title>Marwick Law Letterhead</title>
<link href="https://fonts.googleapis.com/css2?family=Montserrat:wght@400;500;600&display=swap" rel="stylesheet">
<style>
  :root {
    --navy: #182f5a;
    --red: #d71c27;
    --red-deep: #6e0712;
    --ink: #2b2b2b;
    --ink-soft: #3a3a3a;
    --backdrop: #e8e8e8;
    --paper: #ffffff;
  }
  * { margin: 0; padding: 0; box-sizing: border-box; }
  html, body {
    width: 1154px; height: 1200px; overflow: hidden;
    background: var(--backdrop);
    font-family: "Montserrat", Arial, sans-serif;
  }
  .letterhead {
    position: absolute; left: 169px; top: 30px;
    width: 815px; height: 1140px;
    background: var(--paper);
    box-shadow: 0 8px 30px rgba(0,0,0,0.18);
    overflow: hidden;
  }
  .band { position: absolute; left: 0; width: 815px; display: block; }
  .band--top { top: 0; height: 45px; }
  .band--bottom { bottom: 0; height: 52px; }

  .brand {
    position: absolute; left: 31px; top: 94px;
    display: flex; align-items: center; gap: 12px;
  }
  .brand__mark { width: 34px; height: 34px; background: var(--navy); }
  .brand__name {
    font-size: 29px; font-weight: 600; color: var(--navy);
    letter-spacing: 0.5px; line-height: 1;
  }

  .sender, .recipient {
    position: absolute; left: 29px;
    font-size: 13.3px; color: #111; line-height: 17.6px;
  }
  .sender { top: 185px; }
  .recipient { left: 30px; top: 270px; line-height: 20.3px; }

  .body-copy {
    position: absolute; left: 32px; top: 359px; width: 755px;
    font-size: 13.4px; line-height: 20.3px; color: var(--ink-soft);
    text-align: justify;
  }
  .body-copy p + p { margin-top: 20.3px; }

  .closing {
    position: absolute; left: 30px; top: 932px;
    font-size: 15.4px; color: #111;
  }
  .signature {
    position: absolute; left: 29px; top: 958px;
    width: 90px; height: 28px;
    background: linear-gradient(90deg, #e4e4e4, #f2f2f2);
    border-radius: 3px;
  }

  .contact {
    position: absolute; left: 32px; top: 1025px;
    list-style: none; font-size: 13.4px; color: #111;
  }
  .contact li {
    display: flex; align-items: center; gap: 11px;
    height: 20.5px;
  }
  .contact svg { width: 13px; height: 13px; flex: none; }
</style>
</head>
<body>
<main class="letterhead">
  <svg class="band band--top" viewBox="0 0 815 45" preserveAspectRatio="none" aria-hidden="true">
    <defs>
      <linearGradient id="topRed" x1="0" x2="1" y1="0" y2="0">
        <stop offset="0" stop-color="#d71c27"/>
        <stop offset="0.6" stop-color="#d71c27"/>
        <stop offset="1" stop-color="#6e0712"/>
      </linearGradient>
    </defs>
    <polygon points="0,0 465,0 441,45 0,45" fill="#182f5a"/>
    <polygon points="474,0 815,0 815,45 451,45" fill="url(#topRed)"/>
  </svg>

  <div class="brand">
    <span class="brand__mark"></span>
    <span class="brand__name">Marwick Law</span>
  </div>

  <address class="sender" style="font-style:normal">
    1475 Calloway Street,<br>
    Suite 210, Houston,<br>
    Texas 77041
  </address>

  <div class="recipient">
    Mr/s<br>
    First Name and Last Name<br>
    Company Name<br>
    Address
  </div>

  <div class="body-copy">
    <p>Lorem ipsum dolor sit amet,consectetur adipiscing sed do eiusmod tempor incididunt laboreet dolore magna aliqua.Ut enim ad minim.veniam, quis nostrud exercitation ullamco laboris nisi ut aliquip exea commodo consequat.Lorem ipsum dolor sit amet,consectetur adipiscing sed do eiusmod tempor incididunt.labore et dolore magna aliqua. Ut enim</p>
    <p>Lorem ipsum dolor sit amet, consectetur adipiscing sed do eiusmod tempor incididunt labore et dolore magna aliqua. Ut enim ad minim veniam, quis nostrud exercitation ullamco laboris nisi ut aliquip exea commodo consequat.Duis aute irure dolor in reprehenderit in voluptate velit esse cillum irure dolor in reprehenderit in voluptate velit esse irure</p>
    <p>Lorem ipsum dolor sit amet, consectetur adipiscing sed do eiusmod tempor incididunt labore et dolore magna aliqua. consequat. Duis aute irure dolor in.reprehenderit in voluptate velit esse cillum dolore eu fugiat nulla pariatur. Excepteur sint occaecat cupidatat non proident, sunt in culpa qui officia deserunt mollit,</p>
    <p>Lorem ipsum dolor sit amet, consectetur adipiscing sed do eiusmod tempor incididunt labore et dolore magna aliqua. Ut enim Lorem ipsum dolor sit amet, consectetur adipiscing sed do eiusmod tempor incididunt labore et dolore magna aliqua. Ut enim Lorem ipsum aliqua.ipsum</p>
    <p>Lorem ipsum dolor sit amet, consectetur adipiscing sed do eiusmod tempor incididunt labore et dolore magna aliqua. Ut enim ad minim veniam, quis nostrud exercitation ullamco laboris nisi ut aliquip exea commodo consequat.Duis aute irure dolor in reprehenderit in voluptate velit esse cillum irure dolor in reprehenderit in voluptate velit esse irure</p>
    <p>Lorem ipsum dolor sit amet, consectetur adipiscing sed do eiusmod tempor incididunt labore et dolore magna aliqua. Ut enim ad minim veniam, quis nostrud exercitation ullamco laboris nisi ut aliquip exea commodo consequat.Duis aute irure dolor in reprehenderit in voluptate velit esse cillum irure dolor in reprehenderit in voluptate velit esse irure</p>
  </div>

  <div class="closing">Regards</div>
  <div class="signature" role="img" aria-label="Handwritten signature of the sender"></div>

  <ul class="contact">
    <li>
      <svg viewBox="0 0 24 24" aria-hidden="true"><path fill="#d71c27" d="M6.6 10.8c1.4 2.8 3.8 5.1 6.6 6.6l2.2-2.2c.3-.3.7-.4 1-.2 1.1.4 2.3.6 3.6.6.6 0 1 .4 1 1V20c0 .6-.4 1-1 1C10.6 21 3 13.4 3 4c0-.6.4-1 1-1h3.5c.6 0 1 .4 1 1 0 1.3.2 2.5.6 3.6.1.3 0 .7-.2 1l-2.3 2.2z"/></svg>
      <span>832-361-9027</span>
    </li>
    <li>
      <svg viewBox="0 0 24 24" aria-hidden="true"><path fill="#d71c27" d="M6 3h12v5H6zM4 9h16c1.1 0 2 .9 2 2v6h-4v4H6v-4H2v-6c0-1.1.9-2 2-2zm4 7v3h8v-3z"/></svg>
      <span>832-614-7359</span>
    </li>
  </ul>

  <svg class="band band--bottom" viewBox="0 0 815 52" preserveAspectRatio="none" aria-hidden="true">
    <defs>
      <linearGradient id="bottomRed" x1="0" x2="1" y1="0" y2="0">
        <stop offset="0" stop-color="#d71c27"/>
        <stop offset="0.6" stop-color="#d71c27"/>
        <stop offset="1" stop-color="#6e0712"/>
      </linearGradient>
    </defs>
    <polygon points="0,0 436,0 407,52 0,52" fill="#182f5a"/>
    <polygon points="446,0 815,0 815,52 416,52" fill="url(#bottomRed)"/>
  </svg>
</main>
</body>
</html>
```